Quiet Hollow is a cabin in Gatlinburg, Tennessee, near the Ferncrest Ridge National Park. When our cabin was built, there was one thing more important than any other--peace. The front of our cabin is surrounded by woods. It has a huge deck with a swing, Adirondack chairs, and a love seat for relaxation. The back deck has a hot tub, a large round glass table for cocktails or dinner, and because we left no stone unturned, we have a telescope for stargazing. There are two master suites, each have a private bath with a large jetted tub, seperate shower, flat screen TV, and a door that leads to the back deck.

Industry/Entity Type

Business

Contact Information for Business Card

Quiet Hollow Vacation Rentals, LLC
871 Belford Crest Pl.
Oakland, Ky 42159
Janet M. Pruitt, Owner/Manager
(270) 614.2087

```html
<!DOCTYPE html>
<html lang="en">
<head>
<meta charset="utf-8">
<title>Quiet Hollow Vacation Rentals – Business Card</title>
<link href="https://fonts.googleapis.com/css2?family=Open+Sans:wght@400;600;700&display=swap" rel="stylesheet">
<style>
  :root {
    --green: #2aae4a;
    --black: #000000;
    --white: #ffffff;
    --silver: #d9d9d9;
    --backdrop: #8f8f8f;
    --ring: #3a3a3a;
  }
  * { box-sizing: border-box; margin: 0; padding: 0; }
  html, body {
    width: 1200px; height: 900px; overflow: hidden;
    background: var(--backdrop);
    font-family: "Open Sans", Arial, sans-serif;
  }
  .stage { position: relative; width: 1200px; height: 900px; }

  .card {
    position: absolute; left: 250px; width: 700px; height: 400px;
    overflow: hidden; box-shadow: 0 6px 18px rgba(0,0,0,.25);
  }
  .card--front { top: 40px; background: var(--black); }
  .card--back  { top: 470px; background: var(--green); }

  /* front */
  .band { position: absolute; left: 0; width: 100%; background: var(--green); }
  .band--top { top: 0; height: 62px; }
  .band--bottom { bottom: 0; height: 62px; }
  .brand {
    position: absolute; left: 0; right: 0; text-align: center; color: var(--green);
    font-weight: 700; text-transform: uppercase;
  }
  .card--front .brand { top: 110px; }
  .brand__mark {
    display: block; margin: 0 auto 14px; width: 68px; height: 68px;
    border: 4px solid currentColor; border-radius: 50%;
  }
  .brand__name { display: block; font-size: 44px; letter-spacing: 3px; line-height: 1; }
  .brand__tagline { display: block; font-size: 15px; letter-spacing: 1.5px; margin-top: 6px; }

  /* back */
  .card--back .top-panel { position: absolute; top: 0; left: 0; width: 100%; height: 135px; background: var(--black); }
  .card--back .bottom-strip { position: absolute; bottom: 0; left: 0; width: 100%; height: 28px; background: var(--black); }
  .card--back .brand {
    left: auto; right: 40px; top: 14px; width: 270px; color: var(--silver);
  }
  .card--back .brand__mark {
    width: 52px; height: 52px; border: none; background: var(--ring); margin-bottom: 8px;
  }
  .card--back .brand__name { font-size: 30px; letter-spacing: 2px; }
  .card--back .brand__tagline { font-size: 11px; letter-spacing: 1px; margin-top: 4px; }

  .person { position: absolute; left: 34px; top: 148px; color: var(--white); }
  .person__name { font-size: 24px; font-weight: 700; line-height: 1.15; }
  .person__title { font-size: 14px; }

  .contact {
    position: absolute; right: 30px; top: 222px; list-style: none;
    color: var(--white); font-size: 17px; text-align: right; line-height: 1.5;
  }
  .contact li { display: flex; justify-content: flex-end; align-items: center; gap: 10px; }
  .contact svg { width: 13px; height: 13px; fill: var(--white); flex: none; }
</style>
</head>
<body>
<main class="stage">

  <section class="card card--front" aria-label="Card front">
    <div class="band band--top"></div>
    <div class="brand">
      <span class="brand__mark"></span>
      <span class="brand__name">Quiet Hollow</span>
      <span class="brand__tagline">Vacation Rentals, LLC</span>
    </div>
    <div class="band band--bottom"></div>
  </section>

  <section class="card card--back" aria-label="Card back">
    <div class="top-panel"></div>
    <div class="brand">
      <span class="brand__mark"></span>
      <span class="brand__name">Quiet Hollow</span>
      <span class="brand__tagline">Vacation Rentals, LLC</span>
    </div>

    <div class="person">
      <p class="person__name">Janet M. Pruitt</p>
      <p class="person__title">Owner/Manager</p>
    </div>

    <ul class="contact">
      <li>(270) 614.2087
        <svg viewBox="0 0 16 16" aria-hidden="true"><path d="M3 1h3l1 4-2 1a9 9 0 0 0 5 5l1-2 4 1v3a2 2 0 0 1-2 2A13 13 0 0 1 1 3a2 2 0 0 1 2-2z"/></svg></li>
      <li>(270) 614.2087
        <svg viewBox="0 0 16 16" aria-hidden="true"><path d="M4 0h8a1 1 0 0 1 1 1v14a1 1 0 0 1-1 1H4a1 1 0 0 1-1-1V1a1 1 0 0 1 1-1zm1 2v10h6V2zm3 11a1 1 0 1 0 0 2 1 1 0 0 0 0-2z"/></svg></li>
      <li>info@quiethollow-sample.com
        <svg viewBox="0 0 16 16" aria-hidden="true"><path d="M0 3h16v10H0zm1.5 1L8 9l6.5-5z"/></svg></li>
      <li>www.quiethollow-sample.com
        <svg viewBox="0 0 16 16" aria-hidden="true"><path d="M6 10l4-4 1 1-4 4zM4 8l-2 2a2.8 2.8 0 0 0 4 4l2-2-1-1-2 2a1.4 1.4 0 0 1-2-2l2-2zm8 0l2-2a2.8 2.8 0 0 0-4-4L8 4l1 1 2-2a1.4 1.4 0 0 1 2 2l-2 2z"/></svg></li>
      <li>871 Belford Crest Pl., Oakland, Ky 42159
        <svg viewBox="0 0 16 16" aria-hidden="true"><path d="M8 0a5.5 5.5 0 0 1 5.5 5.5C13.5 10 8 16 8 16S2.5 10 2.5 5.5A5.5 5.5 0 0 1 8 0zm0 3a2.5 2.5 0 1 0 0 5 2.5 2.5 0 0 0 0-5z"/></svg></li>
    </ul>

    <div class="bottom-strip"></div>
  </section>

</main>
</body>
</html>
```